Irrigation Business needs their business cards modernised and revamped

I would like to keep my current logo, colours and revamp the format of the card.

I would like the card to be clean yet important.

Im not sure if you include texture but i would like the named logo to be indented into the card etc.

show me something alive and free something thats clinical to the point yet has a feel of achievement. i would like people to go nice card.

Target Market(s)

high end clients, corporate, sports field manger, the guys that make the decisions

Industry/Entity Type

Business

Contact Information for Business Card

nformation to be included

Dean Harlow (Director)
0487305526
dean@kolvat.biz
www.kestonfieldworks.com

instagram logo
google logo
facebook logo

Colors

Designer to choose colors to be used in the design.

Requirements
Nice to have
• indentations a really nice feel to the card good texture

```html
<!DOCTYPE html>
<html lang="en">
<head>
<meta charset="utf-8">
<title>Keston Fieldworks – Business Card</title>
<link rel="stylesheet" href="https://fonts.googleapis.com/css2?family=Open+Sans:wght@400;600;700;800&display=swap">
<style>
  :root {
    --stage: #2a2a2c;
    --green-light: #3fdc91;
    --green-deep: #24a35a;
    --green-text: #2fae5f;
    --blue: #2f6fbf;
    --blue-tab: #3b7bd0;
    --paper: #f7f7f5;
    --ink: #4a4a4a;
    --white: #ffffff;
  }
  * { box-sizing: border-box; margin: 0; padding: 0; }
  html, body {
    width: 1200px; height: 900px; overflow: hidden;
    background: var(--stage);
    font-family: "Open Sans", Arial, sans-serif;
  }
  .canvas {
    position: relative; width: 1200px; height: 900px;
  }
  .card {
    position: absolute; width: 700px; height: 400px;
    left: 250px; overflow: hidden;
    box-shadow: 0 10px 30px rgba(0,0,0,.45);
  }
  .card--front {
    top: 40px;
    background: linear-gradient(100deg, var(--green-light) 0%, var(--green-deep) 60%, var(--green-deep) 100%);
    display: flex; flex-direction: column; align-items: center; justify-content: center;
    color: var(--white);
  }
  .card--back {
    top: 460px;
    background: var(--paper);
  }
  .brand-mark {
    width: 96px; height: 96px; border-radius: 50%;
    background: var(--white);
  }
  .brand-name {
    margin-top: 18px; text-align: center; font-weight: 800;
    line-height: 1.05; text-transform: uppercase;
  }
  .brand-name__main { display: block; font-size: 38px; letter-spacing: .5px; }
  .brand-name__sub { display: block; font-size: 20px; letter-spacing: 12px; margin-top: 4px; }
  .card--front .brand-name { color: var(--white); }
  .social-row { display: flex; gap: 8px; margin-top: 16px; }
  .social-dot { width: 22px; height: 22px; border-radius: 50%; background: var(--white); }

  .tab {
    position: absolute; left: 430px; top: 0; width: 110px; height: 120px;
    background: var(--blue-tab);
  }
  .tab__mark {
    position: absolute; left: 435px; top: 70px; width: 100px; height: 100px;
    border-radius: 50%; background: var(--blue-tab); border: 6px solid var(--paper);
  }
  .card--back .brand-name {
    position: absolute; left: 380px; top: 182px; width: 300px; margin: 0;
    color: var(--blue);
  }
  .card--back .brand-name__main { font-size: 30px; }
  .card--back .brand-name__sub { font-size: 16px; letter-spacing: 10px; }

  .contact { position: absolute; left: 44px; bottom: 40px; color: var(--ink); }
  .contact__name { color: var(--blue); font-weight: 700; font-size: 20px; text-transform: uppercase; }
  .contact__role { color: var(--green-text); font-weight: 600; font-size: 18px; text-transform: uppercase; margin-bottom: 14px; }
  .contact__line { display: flex; align-items: center; gap: 10px; font-size: 17px; line-height: 1.5; }
  .contact__line svg { width: 16px; height: 16px; fill: var(--blue); flex: none; }
</style>
</head>
<body>
<main class="canvas">
  <section class="card card--front" aria-label="Card front">
    <div class="brand-mark" aria-hidden="true"></div>
    <p class="brand-name">
      <span class="brand-name__main">Keston Fieldworks</span>
      <span class="brand-name__sub">Services</span>
    </p>
    <div class="social-row" aria-label="Social profiles">
      <span class="social-dot"></span><span class="social-dot"></span><span class="social-dot"></span>
    </div>
  </section>

  <section class="card card--back" aria-label="Card back">
    <div class="tab" aria-hidden="true"></div>
    <div class="tab__mark" aria-hidden="true"></div>
    <p class="brand-name">
      <span class="brand-name__main">Keston Fieldworks</span>
      <span class="brand-name__sub">Services</span>
    </p>

    <div class="contact">
      <p class="contact__name">Dean Harlow</p>
      <p class="contact__role">Director</p>
      <p class="contact__line">
        <svg viewBox="0 0 16 16" aria-hidden="true"><path d="M3 1h3l1.5 4-2 1.5a9 9 0 0 0 4 4L11 8.5l4 1.5v3a2 2 0 0 1-2 2C6.4 15 1 9.6 1 3a2 2 0 0 1 2-2z"/></svg>
        0487305526
      </p>
      <p class="contact__line">
        <svg viewBox="0 0 16 16" aria-hidden="true"><path d="M1 3h14v10H1z M1 3l7 6 7-6" fill="none" stroke="#2f6fbf" stroke-width="1.8"/></svg>
        dean@kolvat.biz
      </p>
      <p class="contact__line">
        <svg viewBox="0 0 16 16" aria-hidden="true"><circle cx="8" cy="8" r="6.5" fill="none" stroke="#2f6fbf" stroke-width="1.6"/><path d="M1.5 8h13M8 1.5c-3 3.5-3 9.5 0 13M8 1.5c3 3.5 3 9.5 0 13" fill="none" stroke="#2f6fbf" stroke-width="1.2"/></svg>
        kestonfieldworks.com
      </p>
    </div>
  </section>
</main>
</body>
</html>
```